Business card por a urban DJ, up scale audience target

Need a sober design, modern, conservative colors but i can consider some options, y play rnb, hip hop, EDM and top40.

Business card for contact and personal info, double sided, use logo attrached please; im 42 so i need a card acording to my age an target audience.

Target Market(s)

Adult people, up scale audience

Industry/Entity Type

Music Download

Contact Information for Business Card

Cel (318) 4207265518 www.lumadrift.com

Requirements
Must have
• open mind
Nice to have
• open mind
Should not have
• DJ

```html
<!DOCTYPE html>
<html lang="en">
<head>
<meta charset="utf-8">
<title>LUMA — Business Card</title>
<link rel="stylesheet" href="https://fonts.googleapis.com/css2?family=Orbitron:wght@500;800&family=Exo+2:wght@500&display=swap">
<style>
  :root {
    --backdrop: #4b5a62;
    --card-dark: #464646;
    --card-light: #ffffff;
    --ink-light: #ffffff;
    --ink-dark: #464646;
  }
  * { margin: 0; padding: 0; box-sizing: border-box; }
  html, body {
    width: 1200px;
    height: 900px;
    overflow: hidden;
    background: var(--backdrop);
  }
  .canvas {
    position: relative;
    width: 1200px;
    height: 900px;
  }
  .card {
    position: absolute;
    left: 290px;
    width: 620px;
    height: 354px;
    overflow: hidden;
  }
  .card--front { top: 70px; background: var(--card-dark); }
  .card--back  { top: 476px; background: var(--card-dark); }

  .brand {
    position: absolute;
    display: flex;
    flex-direction: column;
    align-items: center;
  }
  .brand__name {
    font-family: "Orbitron", sans-serif;
    font-weight: 800;
    font-size: 92px;
    line-height: 1;
    letter-spacing: 4px;
  }
  .brand__genres {
    margin-top: 18px;
    font-family: "Orbitron", sans-serif;
    font-weight: 800;
    font-size: 17px;
    letter-spacing: 2px;
    word-spacing: 10px;
  }
  .card--front .brand {
    left: 0; right: 0; top: 100px;
    color: var(--ink-light);
  }

  .back__light-panel {
    position: absolute;
    inset: 0;
    background: var(--card-light);
    clip-path: polygon(0 0, 52% 0, 44% 100%, 0 100%);
  }
  .card--back .brand {
    left: 20px; width: 280px; top: 100px;
    color: var(--ink-dark);
  }
  .card--back .brand__name { font-size: 70px; letter-spacing: 3px; }
  .card--back .brand__genres { font-size: 14px; word-spacing: 8px; margin-top: 16px; }

  .contact {
    position: absolute;
    left: 370px;
    top: 150px;
    list-style: none;
    color: var(--ink-light);
    font-family: "Exo 2", sans-serif;
    font-weight: 500;
    font-size: 19px;
    letter-spacing: 1.5px;
  }
  .contact__item {
    display: flex;
    align-items: center;
    gap: 10px;
    height: 26px;
    margin-bottom: 20px;
  }
  .contact__icon { width: 18px; height: 20px; flex: none; }
</style>
</head>
<body>
<main class="canvas">

  <section class="card card--front" aria-label="Card front">
    <div class="brand">
      <span class="brand__name">LUMA</span>
      <span class="brand__genres">RNB HIPHOP EDM</span>
    </div>
  </section>

  <section class="card card--back" aria-label="Card back">
    <div class="back__light-panel"></div>
    <div class="brand">
      <span class="brand__name">LUMA</span>
      <span class="brand__genres">RNB HIPHOP EDM</span>
    </div>
    <ul class="contact">
      <li class="contact__item">
        <svg class="contact__icon" viewBox="0 0 18 20" aria-hidden="true">
          <rect x="4" y="1" width="10" height="18" rx="2" fill="none" stroke="#fff" stroke-width="1.6"/>
          <line x1="4" y1="15" x2="14" y2="15" stroke="#fff" stroke-width="1.2"/>
          <circle cx="9" cy="17" r="0.9" fill="#fff"/>
        </svg>
        <span>(318) 4207265518</span>
      </li>
      <li class="contact__item">
        <svg class="contact__icon" viewBox="0 0 20 20" aria-hidden="true">
          <circle cx="10" cy="10" r="8.5" fill="#fff"/>
          <path d="M6 5c2 1 2 3 0 4s-1 3 1 4 1 3 0 4M12 3c-1 2 1 3 3 3s2 3 0 4-2 3 0 5" fill="none" stroke="#464646" stroke-width="1.6"/>
        </svg>
        <span>www.lumadrift.com</span>
      </li>
    </ul>
  </section>

</main>
</body>
</html>
```